Business Card Design - Amberfield Court

We are looking at a new design for our business cards that has a modern and professional look. We run a residential aged care facility focussing on the care of residents. The cards will be used for potential clients, consultants and business opportunities in this sector. Blue and white is our main colours and would to see these colours incorporated in the design.
Industry/Entity Type
Business
Contact Information for Business Card
Amberfield Court, Darren Walsh, dwalsh@amberfieldcourt.com.au, Finance Manager, 0472 639 208, BCom, 37 Marrabel Crescent, Brindle Vale, Qld 4093.
Look and feel
Each slider illustrates characteristics of the customer's brand and the style your logo design should communicate.

```html
<!DOCTYPE html>
<html lang="en">
<head>
<meta charset="utf-8">
<title>Amberfield Court – Business Card</title>
<link rel="stylesheet" href="https://fonts.googleapis.com/css2?family=Oswald:wght@300&family=Arimo:ital,wght@0,400;0,700;1,400&display=swap">
<style>
  :root {
    --page: #e9ebec;
    --card-white: #ffffff;
    --card-grey: #d9dcde;
    --brand-blue: #4e7b91;
    --brand-blue-light: #7aa0b2;
    --brand-blue-dark: #3f6a80;
    --ink-white: #ffffff;
    --tag-grey: #6f7478;
  }
  * { box-sizing: border-box; margin: 0; padding: 0; }
  html, body { width: 1200px; height: 950px; overflow: hidden; }
  body {
    background: var(--page);
    position: relative;
    font-family: "Arimo", Arial, sans-serif;
  }
  .card {
    position: absolute;
    left: 250px;
    width: 700px;
    height: 400px;
    overflow: hidden;
    box-shadow: 0 10px 28px rgba(0,0,0,0.18);
  }

  /* Back of card */
  .card--back {
    top: 45px;
    background: linear-gradient(135deg, var(--card-white) 0%, var(--card-white) 45%, var(--card-grey) 100%);
    display: flex;
    flex-direction: column;
    align-items: center;
    justify-content: center;
    gap: 18px;
  }
  .brand-mark {
    display: flex;
    align-items: center;
    gap: 16px;
  }
  .brand-mark__dot {
    width: 46px; height: 46px;
    border-radius: 50%;
    background: var(--brand-blue);
  }
  .brand-mark__name {
    font-family: "Oswald", "Arial Narrow", sans-serif;
    font-weight: 300;
    font-size: 44px;
    letter-spacing: 5px;
    color: var(--brand-blue);
    text-transform: uppercase;
  }
  .brand-tagline--back {
    font-style: italic;
    font-size: 22px;
    color: var(--tag-grey);
  }

  /* Front of card */
  .card--front {
    top: 495px;
    background: linear-gradient(120deg, var(--brand-blue-dark) 0%, var(--brand-blue) 45%, var(--brand-blue-light) 75%, var(--brand-blue) 100%);
    color: var(--ink-white);
  }
  .people-art {
    position: absolute;
    left: 0; top: 110px;
    width: 290px; height: 290px;
    background: linear-gradient(90deg, rgba(255,255,255,0.95) 0%, rgba(255,255,255,0.9) 70%, rgba(255,255,255,0) 100%);
    border-top-right-radius: 140px;
  }
  .front-text {
    position: absolute;
    right: 38px; top: 42px;
    text-align: right;
  }
  .front-name {
    font-family: "Oswald", "Arial Narrow", sans-serif;
    font-weight: 300;
    font-size: 36px;
    letter-spacing: 5px;
    text-transform: uppercase;
    line-height: 1.1;
  }
  .front-tagline {
    font-style: italic;
    font-size: 21px;
    margin-top: 2px;
  }
  .person {
    margin-top: 36px;
  }
  .person__name {
    font-weight: 700;
    font-size: 22px;
    letter-spacing: 0.5px;
  }
  .person__name small { font-size: 18px; }
  .person__role {
    font-size: 18px;
    letter-spacing: 0.5px;
  }
  .contact {
    margin-top: 14px;
    font-size: 18px;
    line-height: 1.35;
    letter-spacing: 0.5px;
  }
  .contact__block + .contact__block { margin-top: 14px; }
</style>
</head>
<body>

  <section class="card card--back" aria-label="Card back">
    <div class="brand-mark">
      <span class="brand-mark__dot"></span>
      <span class="brand-mark__name">Amberfield Court</span>
    </div>
    <p class="brand-tagline--back">Comfort, Respect, Community</p>
  </section>

  <section class="card card--front" aria-label="Card front">
    <div class="people-art" role="img" aria-label="White silhouette illustration of two people talking"></div>
    <div class="front-text">
      <h1 class="front-name">Amberfield Court</h1>
      <p class="front-tagline">Comfort, Respect, Community</p>
      <div class="person">
        <p class="person__name">DARREN WALSH <small>BCOM</small></p>
        <p class="person__role">FINANCE MANAGER</p>
      </div>
      <div class="contact">
        <div class="contact__block">
          <p>37 Marrabel Crescent</p>
          <p>Brindle Vale, Qld 4093.</p>
        </div>
        <div class="contact__block">
          <p>0472 639 208</p>
          <p>dwalsh@amberfieldcourt.com.au</p>
          <p>www.amberfieldcourt.com.au</p>
        </div>
      </div>
    </div>
  </section>

</body>
</html>
```